continued... Web Design for Professional Development and marketplace

in addition to the homepages that you are desiging, can you also create designs for the attached wireframes that are part of the same website.
I am creating this as a seperate project as we are keen to see your designs for the rest of the website.
VIdeo of prototype and homepage designs
https://www.quillvane.com/sh/rk7tpa2mw9qhb3c/8Lw2oNv4Zy/design
Updates
added an additional wireframe that was missed in the original upload
added one more wireframe for the homepage: where the user is prompted to login or signup
Industry/Entity Type
Marketplace
Look and feel
Each slider illustrates characteristics of the customer's brand and the style your logo design should communicate.

```html
<!DOCTYPE html>
<html lang="en">
<head>
<meta charset="utf-8">
<title>Favourites – Professional Development Marketplace</title>
<link rel="stylesheet" href="https://fonts.googleapis.com/css2?family=Open+Sans:wght@400;600;700&family=Arimo:wght@400;700&display=swap">
<style>
  :root {
    --page-bg: #f2f2f2;
    --header-bg: #3c3c3c;
    --green: #38996a;
    --green-light: #4db380;
    --mint: #e3f4ec;
    --text-dark: #333333;
    --text-mid: #555555;
    --white: #ffffff;
    --card-border: #3a9a6c;
  }
  * { box-sizing: border-box; margin: 0; padding: 0; }
  html, body { width: 1200px; height: 1159px; overflow: hidden; }
  body { background: var(--page-bg); font-family: "Arimo", Arial, sans-serif; color: var(--text-dark); position: relative; }

  .site { position: absolute; left: 246px; top: 26px; width: 700px; background: var(--white); }

  /* header */
  .topbar { position: relative; height: 50px; background: var(--header-bg); }
  .menu-btn { position: absolute; left: 10px; top: 9px; width: 33px; height: 33px; background: var(--green); }
  .menu-btn span { position: absolute; left: 7px; width: 19px; height: 2px; background: var(--white); }
  .search { position: absolute; left: 53px; top: 9px; width: 163px; height: 33px; background: var(--white); font-size: 12px; padding: 10px 0 0 14px; }
  .search svg { position: absolute; right: 8px; top: 6px; }
  .brand { position: absolute; left: 233px; top: 5px; width: 160px; text-align: center; color: var(--white); font-family: "Open Sans", Arial, sans-serif; }
  .brand-main { font-size: 24px; line-height: 26px; }
  .brand-sub { font-size: 10.5px; line-height: 12px; }
  .btn { position: absolute; top: 9px; height: 33px; width: 81px; font-size: 12px; }
  .btn-review { left: 402px; background: var(--white); color: var(--text-dark); }
  .btn-review svg { position: absolute; left: 8px; top: 9px; }
  .btn-review span { position: absolute; left: 30px; top: 4px; line-height: 12px; font-size: 11.5px; }
  .btn-login { left: 506px; background: var(--green); color: var(--white); }
  .btn-login svg { position: absolute; left: 8px; top: 8px; }
  .btn-login span { position: absolute; left: 28px; top: 9px; }
  .btn-signup { left: 609px; background: var(--white); text-align: center; padding-top: 9px; }

  .subnav { position: relative; height: 26px; background: var(--mint); font-size: 10.5px; color: var(--text-mid); }
  .subnav a { position: absolute; top: 7px; color: inherit; text-decoration: none; }
  .subnav .strong { font-weight: 700; }

  .filters { display: flex; height: 51px; }
  .filter { background: var(--green); color: var(--white); text-align: center; font-size: 12px; padding-top: 10px; line-height: 11px; }
  .filter:nth-child(even) { background: var(--green-light); }
  .filter .arrow { font-size: 7px; line-height: 8px; display: block; }
  .filter .value { font-size: 9px; display: block; }
  .filter .plus { font-size: 18px; display: block; line-height: 20px; }

  /* sections */
  .favourites { position: relative; height: 361px; }
  .page-title { position: absolute; left: 12px; top: 12px; font-size: 19px; font-weight: 700; color: var(--green); }
  .section-sub { position: absolute; left: 12px; top: 41px; font-size: 16px; color: var(--text-dark); }
  .following { position: relative; height: 266px; background: var(--mint); }
  .following .section-title { position: absolute; left: 12px; top: 15px; font-size: 16px; font-weight: 700; color: var(--text-dark); }
  .reviews { position: relative; height: 323px; }

  .board { position: absolute; width: 160px; height: 206px; background: var(--white); border: 1px solid var(--card-border); }
  .board-title { position: absolute; left: 0; right: 0; top: 11px; text-align: center; font-size: 13px; font-weight: 700; color: var(--green); line-height: 16px; letter-spacing: .4px; }
  .board-title small { display: block; font-weight: 400; color: var(--text-dark); font-size: 13px; }
  .board-cover { position: absolute; left: 12px; width: 135px; border: 1px solid var(--card-border); }
  .thumb { position: absolute; top: 154px; width: 41px; height: 41px; border: 1px solid var(--card-border); }

  .tile { position: absolute; background: var(--green); color: var(--white); text-align: center; font-family: "Open Sans", Arial, sans-serif; font-weight: 700; font-size: 18px; line-height: 22px; box-shadow: 0 10px 8px -6px rgba(0,0,0,.35); }
  .tile svg { position: absolute; left: 50%; transform: translateX(-50%); }

  .course { position: absolute; left: 197px; top: 18px; width: 160px; height: 276px; border: 1px solid var(--card-border); background: var(--white); text-align: center; box-shadow: 0 10px 8px -6px rgba(0,0,0,.3); }
  .provider-name { display: flex; align-items: center; justify-content: center; gap: 5px; color: #1f2a5a; font-family: "Open Sans", Arial, sans-serif; font-weight: 600; font-size: 13px; }
  .provider-name i { width: 10px; height: 10px; background: #1f2a5a; display: block; }
  .course-title { position: absolute; top: 68px; left: 0; right: 0; color: var(--green); font-weight: 700; font-size: 13px; line-height: 16px; letter-spacing: .3px; }
  .course-provider { position: absolute; top: 108px; left: 0; right: 0; font-size: 11.5px; }
  .stars { position: absolute; top: 146px; left: 0; right: 0; }
  .formats { position: absolute; top: 188px; left: 0; right: 0; }
  .price { position: absolute; top: 214px; left: 0; right: 0; font-size: 11px; color: #888; }
  .tick { position: absolute; left: 9px; top: 246px; }
</style>
</head>
<body>
<div class="site">
  <header class="topbar">
    <div class="menu-btn"><span style="top:9px"></span><span style="top:15px"></span><span style="top:21px"></span></div>
    <div class="search">Search
      <svg width="22" height="22" viewBox="0 0 22 22"><circle cx="9" cy="9" r="7" fill="none" stroke="#111" stroke-width="2.5"/><line x1="14" y1="14" x2="20" y2="20" stroke="#111" stroke-width="3"/></svg>
    </div>
    <div class="brand"><div class="brand-main">Professional</div><div class="brand-sub">Development Marketplace</div></div>
    <div class="btn btn-review">
      <svg width="16" height="16" viewBox="0 0 16 16"><rect x="6" y="0" width="4" height="16" fill="#333"/><rect x="0" y="6" width="16" height="4" fill="#333"/></svg>
      <span>Add<br>Review</span>
    </div>
    <div class="btn btn-login">
      <svg width="15" height="17" viewBox="0 0 15 17"><circle cx="7.5" cy="5" r="4.5" fill="#fff"/><path d="M0 17 Q0 10 7.5 10 Q15 10 15 17Z" fill="#fff"/></svg>
      <span>Login</span>
    </div>
    <div class="btn btn-signup">Sign up</div>
  </header>

  <nav class="subnav">
    <a class="strong" style="left:218px">About</a>
    <a class="strong" style="left:274px">Business</a>
    <a class="strong" style="left:348px">Developers</a>
    <a style="left:483px">Privacy &amp; Terms</a>
    <a style="left:582px">Copyright &amp; Trademark</a>
  </nav>

  <div class="filters">
    <div class="filter" style="width:71px">Save<span class="plus">+</span></div>
    <div class="filter" style="width:76px">Career<span class="arrow">▼</span><span class="value">(all)</span></div>
    <div class="filter" style="width:108px">Specialization<span class="arrow">▼</span><span class="value">(all)</span></div>
    <div class="filter" style="width:82px">Location<span class="arrow">▼</span><span class="value">(Vancouver)</span></div>
    <div class="filter" style="width:61px">Price<span class="arrow">▼</span><span class="value">($600-3000)</span></div>
    <div class="filter" style="width:94px">Start Date<span class="arrow">▼</span><span class="value">(2 - 6 months)</span></div>
    <div class="filter" style="width:62px">Level<span class="arrow">▼</span><span class="value">(intermediate)</span></div>
    <div class="filter" style="width:69px">Type<span class="arrow">▼</span><span class="value">(multiple)</span></div>
    <div class="filter" style="width:77px">Provider<span class="arrow">▼</span><span class="value">(one)</span></div>
  </div>

  <section class="favourites">
    <h1 class="page-title">Favourites</h1>
    <h2 class="section-sub" style="font-weight:400">Your Boards</h2>

    <div class="board" style="left:14px;top:73px">
      <div class="board-title">Medical</div>
      <div class="board-cover" role="img" aria-label="Photo of doctors reviewing notes" style="top:37px;height:104px;background:linear-gradient(135deg,#cfe0ea,#f4f6f8 55%,#a9bfd0)"></div>
      <div class="thumb" role="img" aria-label="Surgeon in mask" style="left:12px;background:linear-gradient(#e6d9cf,#cfc6c0)"></div>
      <div class="thumb" role="img" aria-label="Blood sample tube" style="left:60px;background:linear-gradient(#ece8e6,#c9b7b2)"></div>
      <div class="thumb" role="img" aria-label="Pill bottle" style="left:107px;background:linear-gradient(135deg,#6b3a10,#d9d6d2)"></div>
    </div>

    <div class="board" style="left:196px;top:73px">
      <div class="board-title">Marketing</div>
      <div class="board-cover" role="img" aria-label="Hand holding a marketing word sphere" style="top:37px;height:104px;background:linear-gradient(120deg,#f2f2ee,#e4ece2 50%,#4a4a4a)"></div>
      <div class="thumb" role="img" aria-label="Calculator" style="left:12px;background:linear-gradient(#9aa4b4,#4d4d55)"></div>
      <div class="thumb" role="img" aria-label="Pen on document" style="left:60px;background:linear-gradient(#f4f4f4,#cfcfcf)"></div>
      <div class="thumb" role="img" aria-label="Bar chart" style="left:107px;background:#f4f7f4">
        <svg width="39" height="39" viewBox="0 0 39 39"><rect x="4" y="26" width="6" height="9" fill="#3aa3d8"/><rect x="12" y="20" width="6" height="15" fill="#e33"/><rect x="20" y="14" width="6" height="21" fill="#f5b21b"/><rect x="28" y="8" width="6" height="27" fill="#4cb848"/></svg>
      </div>
    </div>

    <div class="tile" style="left:370px;top:73px;width:161px;height:207px;padding-top:22px">Add New<br>Board
      <svg style="top:102px" width="70" height="70" viewBox="0 0 70 70"><circle cx="35" cy="35" r="31" fill="none" stroke="#fff" stroke-width="7"/><rect x="29" y="17" width="12" height="36" fill="#fff"/><rect x="17" y="29" width="36" height="12" fill="#fff"/></svg>
    </div>
  </section>

  <section class="following">
    <h2 class="section-title">Boards you are following</h2>

    <div class="board" style="left:14px;top:48px">
      <div class="board-title">Keystone<br>Marketing</div>
      <div class="board-cover" style="top:49px;height:92px;display:flex;align-items:center;justify-content:center">
        <div class="provider-name"><i></i>Keystone Marketing</div>
      </div>
      <div class="thumb" style="left:12px"></div>
      <div class="thumb" style="left:60px"></div>
      <div class="thumb" style="left:107px"></div>
    </div>

    <div class="board" style="left:196px;top:48px">
      <div class="board-title">My Reco’s<small>by Dr Harlow</small></div>
      <div class="board-cover" role="img" aria-label="Portrait of the board author" style="top:49px;height:92px;background:radial-gradient(circle at 50% 40%,#b98f78,#6d6f73 60%,#33363a)"></div>
      <div class="thumb" style="left:12px"></div>
      <div class="thumb" style="left:60px"></div>
      <div class="thumb" style="left:107px"></div>
    </div>
  </section>

  <section class="reviews">
    <div class="tile" style="left:14px;top:18px;width:160px;height:137px;padding-top:22px">Add Review
      <svg style="top:50px" width="70" height="70" viewBox="0 0 70 70"><circle cx="35" cy="35" r="31" fill="none" stroke="#fff" stroke-width="7"/><rect x="29" y="17" width="12" height="36" fill="#fff"/><rect x="17" y="29" width="36" height="12" fill="#fff"/></svg>
    </div>

    <article class="course">
      <div class="provider-name" style="margin-top:24px">Keystone Marketing</div>
      <div class="course-title">Product Management<br>Foucus</div>
      <div class="course-provider">Keystone Marketing</div>
      <div class="stars">
        <svg width="92" height="16" viewBox="0 0 92 16" fill="#38996a">
          <path id="s" d="M8 0l2.4 5.2 5.6.6-4.2 3.8 1.2 5.6L8 12.3 3 15.2l1.2-5.6L0 5.8l5.6-.6z"/>
          <use href="#s" x="19"/><use href="#s" x="38"/><use href="#s" x="57"/><use href="#s" x="76"/>
        </svg>
      </div>
      <div class="formats">
        <svg width="72" height="20" viewBox="0 0 72 20" fill="#38996a">
          <path d="M2 12l10-8 8 3-10 8z M2 13l8 4 10-8v2l-10 8-8-4z"/>
          <circle cx="36" cy="5" r="4"/><circle cx="29" cy="8" r="3"/><circle cx="43" cy="8" r="3"/>
          <path d="M28 18q0-8 8-8t8 8z M23 18q0-6 6-6v6z M49 18q0-6-6-6v6z"/>
          <rect x="54" y="2" width="16" height="11" rx="1" fill="none" stroke="#38996a" stroke-width="2"/><rect x="60" y="13" width="4" height="4"/><rect x="57" y="17" width="10" height="2"/>
        </svg>
      </div>
      <div class="price">$995</div>
      <svg class="tick" width="24" height="20" viewBox="0 0 24 20"><path d="M2 10l7 7L22 2" fill="none" stroke="#38996a" stroke-width="4"/></svg>
    </article>
  </section>
</div>
</body>
</html>
```